Redesign of business card for Cedar Ridge Mechanical

We are looking for a new design for our business cards for Cedar Ridge Mechanical. We are a plumbing & HVAC construction company, operating on the West Coast of Canada and USA. Logo attached.
Industry/Entity Type
Construction - Plumbing & HVAC
Contact Information for Business Card
Name, address, phone numbers, email, website address
Look and feel
Each slider illustrates characteristics of the customer's brand and the style your logo design should communicate.

```html
<!DOCTYPE html>
<html lang="en">
<head>
<meta charset="utf-8">
<title>Cedar Ridge Mechanical – Business Card</title>
<link rel="stylesheet" href="https://fonts.googleapis.com/css2?family=Montserrat:wght@400;500;700&display=swap">
<style>
  :root {
    --bg: #0d0d0d;
    --card: #1b1b1b;
    --card-edge: #262626;
    --pattern: #222222;
    --ink: #ffffff;
    --ink-soft: #d9d9d9;
    --rule: #bfbfbf;
  }
  * { box-sizing: border-box; margin: 0; padding: 0; }
  html, body {
    width: 1200px; height: 963px; overflow: hidden;
    background: var(--bg);
    font-family: "Montserrat", sans-serif;
    color: var(--ink);
  }
  .canvas {
    width: 1200px; height: 963px;
    display: flex; flex-direction: column;
    align-items: center; justify-content: center; gap: 60px;
  }
  .card {
    position: relative;
    width: 630px; height: 360px;
    background: var(--card);
    border: 1px solid var(--card-edge);
    border-radius: 24px;
    overflow: hidden;
    box-shadow: 0 18px 40px rgba(0,0,0,.6);
  }

  /* Front */
  .front .rule-long {
    position: absolute; left: 44px; top: 180px;
    width: 300px; height: 1px; background: var(--rule);
  }
  .front .rule-short {
    position: absolute; right: 44px; top: 214px;
    width: 230px; height: 1px; background: var(--rule);
  }
  .front .brand {
    position: absolute; right: 44px; top: 108px;
    display: flex; align-items: center; gap: 12px;
  }
  .brand-square { width: 18px; height: 18px; background: var(--ink); }
  .brand-name {
    font-weight: 700; font-size: 20px; letter-spacing: .06em;
    text-transform: uppercase; color: var(--ink);
    white-space: nowrap;
  }
  .front .person {
    position: absolute; right: 44px; top: 148px; text-align: right;
  }
  .person-name { font-weight: 700; font-size: 22px; letter-spacing: .03em; line-height: 1.2; }
  .person-title { font-weight: 400; font-size: 15px; margin-top: 2px; color: var(--ink-soft); }
  .front .address {
    position: absolute; right: 44px; top: 228px; text-align: right;
    font-size: 16px; line-height: 1.35; color: var(--ink-soft);
  }
  .front .contacts {
    position: absolute; left: 44px; top: 198px;
    list-style: none; display: flex; flex-direction: column; gap: 8px;
    font-size: 16px; color: var(--ink-soft);
  }
  .contacts li { display: flex; align-items: center; gap: 10px; white-space: nowrap; }
  .contacts svg { width: 16px; height: 16px; fill: var(--ink); flex: none; }

  /* Back */
  .back .pattern {
    position: absolute; inset: 0;
    background: radial-gradient(circle at 50% 50%, var(--pattern), var(--card) 75%);
  }
  .back .brand {
    position: absolute; inset: 0;
    display: flex; align-items: center; justify-content: center; gap: 16px;
  }
  .back .brand-square { width: 26px; height: 26px; }
  .back .brand-name { font-size: 30px; }
</style>
</head>
<body>
<main class="canvas">
  <section class="card front" aria-label="Business card front">
    <div class="brand">
      <span class="brand-square"></span>
      <span class="brand-name">Cedar Ridge Mechanical</span>
    </div>
    <div class="person">
      <p class="person-name">DANIEL HAYES</p>
      <p class="person-title">Manager</p>
    </div>
    <div class="rule-long"></div>
    <div class="rule-short"></div>
    <ul class="contacts">
      <li>
        <svg viewBox="0 0 24 24" aria-hidden="true"><path d="M6.6 10.8a15.1 15.1 0 0 0 6.6 6.6l2.2-2.2a1 1 0 0 1 1-.25 11.4 11.4 0 0 0 3.6.57 1 1 0 0 1 1 1V20a1 1 0 0 1-1 1A17 17 0 0 1 3 4a1 1 0 0 1 1-1h3.5a1 1 0 0 1 1 1c0 1.25.2 2.45.57 3.57a1 1 0 0 1-.25 1z"/></svg>
        604-555-0148
      </li>
      <li>
        <svg viewBox="0 0 24 24" aria-hidden="true"><path d="M3 5h18a1 1 0 0 1 1 1v12a1 1 0 0 1-1 1H3a1 1 0 0 1-1-1V6a1 1 0 0 1 1-1zm9 7.2L20 7H4z"/></svg>
        hello@cedarridgemech.ca
      </li>
      <li>
        <svg viewBox="0 0 24 24" aria-hidden="true"><path d="M12 2a10 10 0 1 0 0 20 10 10 0 0 0 0-20zm6.9 9h-3a15 15 0 0 0-1.3-5.6A8 8 0 0 1 18.9 11zM12 4.1c.9 1.2 1.8 3.6 1.9 6.9h-3.8c.1-3.3 1-5.7 1.9-6.9zM9.4 5.4A15 15 0 0 0 8.1 11h-3a8 8 0 0 1 4.3-5.6zM5.1 13h3a15 15 0 0 0 1.3 5.6A8 8 0 0 1 5.1 13zM12 19.9c-.9-1.2-1.8-3.6-1.9-6.9h3.8c-.1 3.3-1 5.7-1.9 6.9zm2.6-1.3a15 15 0 0 0 1.3-5.6h3a8 8 0 0 1-4.3 5.6z"/></svg>
        www.cedarridgemech.ca
      </li>
    </ul>
    <p class="address">1450 Harbor Way,<br>Surrey BC, V3S 0A1</p>
  </section>

  <section class="card back" aria-label="Business card back">
    <div class="pattern" role="img" aria-label="Faint repeating brand pattern across the card background"></div>
    <div class="brand">
      <span class="brand-square"></span>
      <span class="brand-name">Cedar Ridge Mechanical</span>
    </div>
  </section>
</main>
</body>
</html>
```